Upmarket Dessert Lounge needs a Business Card Design

We are an upmarket dessert lounge needing a business card to match our image.

We want something that is simple yet beautiful, feminine, classy, sophisticated and elegant. We want it to stand out and don't mind if it is bold.

The design should include our logo and colours of red or maroon with gold highlights. We don't mind if black is used.

Marlow & Quince

Target Market(s)

For those who like to indulge or treat themselves and give in to their temptations on good quality desserts.

Industry/Entity Type

Business

Requirements
Must have
• Must include our logo and our name

Marlow & Quince

M & Q

```html
<!DOCTYPE html>
<html lang="en">
<head>
<meta charset="utf-8">
<title>Marlow &amp; Quince — Business Card</title>
<link rel="stylesheet" href="https://fonts.googleapis.com/css2?family=Open+Sans:wght@400;600&display=swap">
<style>
  :root {
    --backdrop: #f2e6e8;
    --card-red: #9b2424;
    --card-red-deep: #6e1616;
    --badge-red: #7a1b1b;
    --gold: #e9b878;
    --gold-light: #f6d9a8;
    --gold-dark: #b57a3c;
    --ivory: #fbeee0;
    --shadow: rgba(60, 20, 20, 0.28);
  }
  * { box-sizing: border-box; margin: 0; padding: 0; }
  html, body {
    width: 1200px;
    height: 951px;
    overflow: hidden;
    background: var(--backdrop);
    font-family: "Open Sans", Arial, sans-serif;
  }
  .canvas {
    position: relative;
    width: 1200px;
    height: 951px;
  }
  .card {
    position: absolute;
    width: 580px;
    height: 330px;
    border-radius: 22px;
    background: var(--card-red);
    box-shadow: 0 14px 30px var(--shadow);
    overflow: hidden;
  }
  .card--front { left: 80px; top: 80px; }
  .card--back { left: 540px; top: 520px; }

  .edge-band {
    position: absolute;
    top: 0;
    bottom: 0;
    width: 16px;
    background: linear-gradient(90deg, var(--gold-dark), var(--gold-light) 50%, var(--gold-dark));
  }
  .edge-band--left { left: 0; }
  .edge-band--right { right: 0; }

  /* Ornamental frame area: flat gradient placeholder */
  .ornament-frame {
    position: absolute;
    border-radius: 60px;
    background: radial-gradient(ellipse at center, var(--badge-red) 0%, var(--card-red-deep) 100%);
    box-shadow: inset 0 0 0 2px rgba(233, 184, 120, 0.35);
  }
  .ornament-frame--front { left: 130px; top: 58px; width: 320px; height: 150px; }
  .ornament-frame--back { left: 40px; top: 96px; width: 200px; height: 138px; border-radius: 48px; }

  .brand-name {
    position: absolute;
    left: 130px;
    width: 320px;
    top: 58px;
    height: 150px;
    display: flex;
    align-items: center;
    justify-content: center;
    color: var(--gold);
    font-weight: 600;
    font-size: 30px;
    letter-spacing: 1px;
  }
  .website {
    position: absolute;
    left: 0;
    right: 0;
    top: 256px;
    text-align: center;
    color: var(--gold);
    font-size: 17px;
    letter-spacing: 2px;
  }

  .monogram {
    position: absolute;
    left: 40px;
    top: 96px;
    width: 200px;
    height: 138px;
    display: flex;
    align-items: center;
    justify-content: center;
    color: var(--gold);
    font-weight: 600;
    font-size: 50px;
  }
  .contact {
    position: absolute;
    right: 44px;
    top: 98px;
    text-align: right;
    color: var(--ivory);
    font-size: 16px;
    line-height: 1.3;
  }
  .contact__name {
    color: var(--gold);
    font-size: 23px;
    margin-bottom: 18px;
  }
  .contact__address { margin-bottom: 16px; }
  .contact .accent { color: var(--gold); }
</style>
</head>
<body>
<main class="canvas">

  <section class="card card--front" aria-label="Business card front">
    <span class="edge-band edge-band--left"></span>
    <span class="edge-band edge-band--right"></span>
    <div class="ornament-frame ornament-frame--front" role="img" aria-label="Ornate gold scroll frame around the brand name"></div>
    <p class="brand-name">Marlow &amp; Quince</p>
    <p class="website">www.marlowquince.com</p>
  </section>

  <section class="card card--back" aria-label="Business card back">
    <span class="edge-band edge-band--right"></span>
    <div class="ornament-frame ornament-frame--back" role="img" aria-label="Ornate gold scroll frame around the monogram"></div>
    <p class="monogram">M &amp; Q</p>
    <div class="contact">
      <p class="contact__name">Marlow &amp; Quince</p>
      <p class="contact__address">48 Harlan Street, Suite 410<br>Northfield, Ohio 44067</p>
      <p class="contact__phone">330-555-0142</p>
      <p class="contact__email">info@<span class="accent">marlowquince</span>.com</p>
    </div>
  </section>

</main>
</body>
</html>
```